Compelling Senior Home Care highlight live-in home care and couples care

Compelling High end client who is looking to advertise and highlight their live-in home care and couples care. Their name is Meadowlark Home Health Services and their website is https://www.meadowlarkhhs-example.com/ Please use their current website colors and I attached some examples.

Specs:

Non-Medical Care or
Home Health Grid Ad
3.85w x 3h

Ad should have:
LOGO
WEBSITE
PHONE NUMBER
(BUTTON - Find Out More)
Text Variations:
We Give People the Help They Need to Live in the Place They Love (see example for exact look and feel)
Do you or your loved one need care at home?
Live at home as long as possible!
Caregivers You Can Trust
Caregivers That Come On Time
Caregivers That Live with You
High Level Care
Hours Match Your Needs

PVG is produced in Macintosh platform CS6. Please create your ads in these programs. Please submit
your ads in high-resolution camera-ready PDF, TIF or EPS format: 300 DPI at 100% of printed size, all
colors CMYK, all fonts and graphics embedded. Use POSTSCRIPT TYPE 1 fonts when possible, TRUE TYPE
FONTS may not print correctly. If submitting native files, please include all linked graphics and fonts.
NOTE: if your ad is not produced by the PVG Art Staff, a professional Ad Agency or Design firm, and is
not properly constructed for technical electronic digital printing, the final printed product may not print
correctly and may differ from your screen proof. Please flightcheck your ad before submitting to PVG.
Publisher reserves the right to charge for all costs incurred in preparation of material submitted that
does not meet the Elders Pine Guide digital specifications.
• All colors, logos, and images in your ad need to be CMYK builds at 300 dpi at 100% size
• Construct your file document size to our size specifications and save your PDF to 100% of size

Target Market(s)

Adults taking care of mom and dad

Industry/Entity Type

Home Health Care

Requirements
Nice to have
• PLEASE SEE EXAMPLES
Should not have
• BORING

```html
<!DOCTYPE html>
<html lang="en">
<head>
<meta charset="utf-8">
<title>Meadowlark Home Health Services – Senior Home Care Ad</title>
<link rel="stylesheet" href="https://fonts.googleapis.com/css2?family=Lobster&family=Montserrat:wght@400;600;700&family=Source+Sans+3:wght@700&display=swap">
<style>
  :root {
    --plum: #6b1446;
    --magenta: #c44a9c;
    --pink-soft: #e9a3c9;
    --hot-pink: #e0148c;
    --white: #ffffff;
    --backdrop: #e6e6e6;
  }
  * { margin: 0; padding: 0; box-sizing: border-box; }
  html, body {
    width: 1200px;
    height: 997px;
    overflow: hidden;
    background: var(--backdrop);
  }
  .ad {
    position: absolute;
    left: 0;
    top: 33px;
    width: 1200px;
    height: 930px;
    background: var(--plum);
    overflow: hidden;
  }
  .ad__shapes {
    position: absolute;
    inset: 0;
    width: 100%;
    height: 100%;
  }
  .ad__tagline {
    position: absolute;
    left: 52px;
    top: 104px;
    font-family: "Lobster", cursive;
    font-size: 34px;
    color: var(--pink-soft);
    white-space: nowrap;
  }
  .ad__headline {
    position: absolute;
    left: 52px;
    top: 164px;
    font-family: "Source Sans 3", sans-serif;
    font-weight: 700;
    font-size: 72px;
    line-height: 76px;
    color: var(--white);
    white-space: nowrap;
  }
  .ad__rule {
    position: absolute;
    left: 52px;
    top: 362px;
    width: 178px;
    height: 3px;
    background: var(--white);
  }
  .ad__offer {
    position: absolute;
    left: 52px;
    top: 392px;
    font-family: "Montserrat", sans-serif;
    font-weight: 400;
    font-size: 28px;
    line-height: 41px;
    color: var(--white);
    white-space: nowrap;
  }
  .ad__offer-lead {
    font-weight: 600;
    color: var(--pink-soft);
  }
  .ad__phone {
    position: absolute;
    left: 64px;
    top: 547px;
    width: 410px;
    height: 56px;
    background: var(--magenta);
    border-radius: 28px 10px 4px 28px;
  }
  .ad__phone-icon {
    position: absolute;
    left: -1px;
    top: -2px;
    width: 60px;
    height: 60px;
  }
  .ad__phone-number {
    position: absolute;
    left: 79px;
    top: 0;
    line-height: 56px;
    font-family: "Montserrat", sans-serif;
    font-weight: 700;
    font-size: 44px;
    color: var(--white);
    white-space: nowrap;
  }
  .ad__cta {
    position: absolute;
    left: 64px;
    top: 620px;
    height: 44px;
    padding: 0 28px;
    border-radius: 22px;
    background: var(--white);
    font-family: "Montserrat", sans-serif;
    font-weight: 700;
    font-size: 20px;
    line-height: 44px;
    color: var(--plum);
    text-decoration: none;
    white-space: nowrap;
  }
  .ad__brand {
    position: absolute;
    left: 52px;
    top: 782px;
    display: flex;
    align-items: center;
    gap: 18px;
  }
  .ad__brand-mark {
    width: 66px;
    height: 66px;
    background: var(--plum);
  }
  .ad__brand-name {
    font-family: "Montserrat", sans-serif;
    font-weight: 700;
    font-size: 28px;
    line-height: 34px;
    color: var(--plum);
  }
  .ad__website {
    position: absolute;
    left: 52px;
    top: 868px;
    font-family: "Montserrat", sans-serif;
    font-weight: 600;
    font-size: 19px;
    line-height: 24px;
    color: var(--magenta);
    white-space: nowrap;
  }
</style>
</head>
<body>
  <main class="ad">
    <svg class="ad__shapes" viewBox="0 0 1159 898" preserveAspectRatio="none">
      <defs>
        <linearGradient id="photoTones" x1="0" y1="0" x2="1" y2="1">
          <stop offset="0" stop-color="#9c7a5c"/>
          <stop offset="0.45" stop-color="#5f6e66"/>
          <stop offset="0.8" stop-color="#3f4f4c"/>
          <stop offset="1" stop-color="#c9a98a"/>
        </linearGradient>
      </defs>
      <path class="band band--upper" fill="#c44a9c"
        d="M1159,87 C820,110 510,370 455,640 C440,740 520,840 600,898 L1159,898 Z"/>
      <g role="img" aria-label="Photo of a smiling senior couple embracing at a kitchen table with a coffee mug">
        <path class="photo" fill="url(#photoTones)" stroke="#ffffff" stroke-width="8"
          d="M1159,157 C850,175 560,380 495,640 C474,730 475,820 482,898 L1159,898 Z"/>
      </g>
      <path class="band band--lower" fill="#c44a9c"
        d="M0,667 C230,630 470,710 600,898 L0,898 Z"/>
      <path class="base" fill="#ffffff"
        d="M0,676 C215,648 435,722 535,898 L0,898 Z"/>
    </svg>

    <p class="ad__tagline">The Premier Private Home Care Provider</p>
    <h1 class="ad__headline">Senior Home Care<br>&amp; Couples Care</h1>
    <div class="ad__rule"></div>
    <p class="ad__offer"><span class="ad__offer-lead">Live-in care available.</span><br>Receive a complimentary<br>home care assessment today!</p>

    <div class="ad__phone">
      <svg class="ad__phone-icon" viewBox="0 0 60 60" aria-hidden="true">
        <circle cx="30" cy="30" r="27" fill="#e0148c" stroke="#ffffff" stroke-width="4"/>
        <circle cx="30" cy="30" r="17" fill="#ffffff"/>
        <path fill="#e0148c"
          d="M24.5,20.5 l3,-1 2.5,5.2 -2.2,1.8 c0.9,2.6 2.6,4.4 5,5.4 l1.9,-2.2 5.1,2.7 -1,3 c-0.4,1.1 -1.5,1.7 -2.6,1.5 c-6.5,-1.2 -11.3,-6.1 -12.3,-12.6 c-0.2,-1.1 0.4,-2.1 1.4,-2.5 z"/>
      </svg>
      <span class="ad__phone-number">555-214-0387</span>
    </div>

    <a class="ad__cta" href="https://www.meadowlarkhhs-example.com/">Find Out More</a>

    <div class="ad__brand">
      <div class="ad__brand-mark"></div>
      <p class="ad__brand-name">Meadowlark<br>Home Health Services</p>
    </div>
    <p class="ad__website">www.meadowlarkhhs-example.com</p>
  </main>
</body>
</html>
```